Lorvex Tilo medical cannibis cultivation company

tag - Tilo rise
Lorvex Tilo medical cannabis cultivation - logo is selected- can we please see bold examples with our selection. We are mainly dealing with medical companies and professionals. We would like to be stand out in the crowd with our designs. Welcome any and all attempts. Thanks

Target Market(s)

Medical and Professional

Industry/Entity Type

Medical And Science

Font styles to use
Sans Serif

Colors

Designer to choose colors to be used in the design.

Requirements
Must have
• Bright colour and be bold- Love the teal and magenta that is currently on the dark background design.
Nice to have
• shading and the 3D affect- The shadowed appearance.
Should not have
• Anything related to illegal activity or un professional manners

```html
<!DOCTYPE html>
<html lang="en">
<head>
<meta charset="utf-8">
<title>Lorvex Tilo Stationery</title>
<link href="https://fonts.googleapis.com/css2?family=Questrial&family=Roboto:wght@400;500&display=swap" rel="stylesheet">
<style>
  :root {
    --backdrop: #dcdcdc;
    --paper: #f6f6f6;
    --magenta: #9b4a99;
    --teal: #1d8a80;
    --rule-grey: #8e9296;
    --ink: #4a4a4a;
    --ink-soft: #5b5b5b;
    --flap: #000000;
  }
  * { box-sizing: border-box; margin: 0; padding: 0; }
  html, body { width: 1200px; height: 877px; overflow: hidden; }
  body {
    background: var(--backdrop);
    font-family: "Questrial", sans-serif;
    color: var(--ink);
    position: relative;
  }
  .sheet {
    position: absolute;
    background: var(--paper);
    box-shadow: 0 1px 3px rgba(0,0,0,0.18);
    overflow: hidden;
  }
  .edge-band { position: absolute; left: 0; top: 0; }

  .brand {
    position: absolute;
    display: flex; flex-direction: column; align-items: center;
  }
  .brand-ring {
    border-radius: 50%;
    border: 3px solid var(--rule-grey);
  }
  .brand-name {
    font-family: "Questrial", sans-serif;
    color: var(--teal);
    font-size: 16px; letter-spacing: 0.3px;
    text-transform: uppercase;
    line-height: 16px;
    white-space: nowrap;
  }
  .brand-tag {
    font-family: "Questrial", sans-serif;
    color: var(--rule-grey);
    font-size: 6.5px; letter-spacing: 1px; text-transform: uppercase;
    line-height: 7px;
    white-space: nowrap;
    display: flex; align-items: center; gap: 4px;
  }
  .brand-tag::before, .brand-tag::after {
    content: ""; width: 18px; height: 1px; background: var(--rule-grey);
  }

  /* Letterhead */
  .letterhead { left: 60px; top: 66px; width: 528px; height: 742px; }
  .letterhead .brand { left: 204px; top: 42px; width: 120px; }
  .letterhead .brand-ring { width: 54px; height: 54px; }
  .letterhead .brand-name { margin-top: 7px; }
  .letterhead .brand-tag { margin-top: 2px; }
  .salutation {
    position: absolute; left: 47px; top: 208px;
    font-size: 13px; color: var(--ink);
  }
  .letter-body {
    position: absolute; left: 47px; top: 247px; width: 440px;
    font-size: 7.6px; line-height: 11.4px; color: var(--ink-soft);
    text-align: justify;
  }
  .letter-body p + p { margin-top: 11.4px; }
  .closing {
    position: absolute; left: 47px; top: 486px;
    font-size: 7.4px; color: var(--ink-soft);
  }
  .signature {
    position: absolute; left: 42px; top: 518px; width: 96px; height: 40px;
    background: linear-gradient(90deg, rgba(42,90,168,0.25), rgba(42,90,168,0.1));
    border-radius: 4px;
  }
  .letter-footer {
    position: absolute; left: 0; top: 688px; width: 528px;
    text-align: center;
    font-family: "Roboto", sans-serif;
    font-size: 8.4px; line-height: 11.2px; color: var(--ink-soft);
  }
  .letter-footer b { color: var(--magenta); font-weight: 500; }

  /* Envelope back */
  .envelope-back { left: 614px; top: 299px; width: 532px; height: 241px; }
  .envelope-flap { position: absolute; left: 0; top: 0; }
  .flap-mark {
    position: absolute; left: 258px; top: 30px;
    width: 16px; height: 16px; border-radius: 50%;
    background: var(--teal);
  }

  /* Envelope front */
  .envelope-front { left: 615px; top: 567px; width: 531px; height: 241px; }
  .envelope-front .brand { left: 18px; top: 25px; width: 120px; }
  .envelope-front .brand-ring { width: 50px; height: 50px; }
  .envelope-front .brand-name { margin-top: 5px; }
  .envelope-front .brand-tag { margin-top: 1px; }
  .return-address {
    position: absolute; left: 18px; top: 107px; width: 120px;
    text-align: center;
    font-family: "Roboto", sans-serif;
    font-size: 8.4px; line-height: 10.6px; color: var(--ink-soft);
  }
</style>
</head>
<body>

<section class="sheet letterhead">
  <svg class="edge-band" width="60" height="742" viewBox="0 0 60 742" aria-hidden="true">
    <path d="M0 0 H40 C24 200 18 420 42 742 H0 Z" fill="var(--magenta)"/>
    <path d="M48 0 C32 200 26 420 50 742" fill="none" stroke="var(--rule-grey)" stroke-width="3"/>
  </svg>

  <div class="brand">
    <div class="brand-ring"></div>
    <div class="brand-name">Lorvex Tilo</div>
    <div class="brand-tag">Tilo rise</div>
  </div>

  <p class="salutation">Dear Ms. Quell,</p>

  <div class="letter-body">
    <p>Lorem ipsum dolor sit amet, consectetur adipiscing elit. Donec orci purus, luctus vitae dignissim eu, iaculis sed purus. Vivamus faucibus, ipsum nec aliquet viverra, leo mauris condimentum ligula, sit amet sagittis enim ligula quis arcu. Nam egestas tortor id nisi porttitor mattis. In tortor ante, ultricies in suscipit a, tempus non massa. Vivamus et auctor mi. Fusce vel massa nulla. Phasellus nec eros mauris, et scelerisque orci.</p>
    <p>Donec malesuada orci vitae nulla accumsan porta a id massa. Quisque accumsan iaculis magna sit amet fringilla. Maecenas consequat, magna eget tincidunt semper, odio nibh rutrum mi, id feugiat ante nisi eu risus. Vestibulum nunc orci, rhoncus a placerat in, ultricies in mi. Cras mattis varius eros, vel fringilla nisi suscipit eget. Quisque scelerisque sagittis nulla at porttitor.</p>
    <p>Sed id augue vitae urna euismod commodo aliquet a quam. Pellentesque arcu velit, cursus et malesuada ut, consequat et diam. Nullam erat sem, rhoncus id ullamcorper vitae, rhoncus et arcu. In ultricies ultricies nulla, ut rutrum nisi iaculis at. Donec eu magna a metus ornare faucibus. Fusce aliquet faucibus ultricies. Morbi semper, est id tincidunt gravida, sem arcu adipiscing lacus, ac bibendum nulla leo eu purus. Quisque nec diam sed risus consectetur a ccumsan quis quis nibh. Vestibulum id purus lorem.</p>
    <p>It is a long established fact that a reader will be distracted by the readable content of a page when looking at its layout. The point of using Lorem Ipsum is that it has a more-or-less normal distribution of letters, as opposed to using 'Content here, content here', making it look like readable English. Many desktop publishing packages</p>
  </div>

  <p class="closing">Sincerely,</p>
  <div class="signature" role="img" aria-label="Handwritten signature of Mara Quell"></div>

  <div class="letter-footer">
    <div>2140 Fernhill Road, Ashby, Oregon 58210</div>
    <div><b>P:</b> 555 210 4471 <b>C:</b> 555 318 9026 <b>F:</b> 555 742 6635 <b>E:</b> mara@lorvextilo.com</div>
    <div><b>W:</b> www.lorvextilo.com</div>
  </div>
</section>

<section class="sheet envelope-back">
  <svg class="envelope-flap" width="532" height="78" viewBox="0 0 532 78" aria-hidden="true">
    <path d="M0 0 H532 L526 40 Q518 74 484 74 H48 Q14 74 6 40 Z" fill="var(--flap)"/>
  </svg>
  <div class="flap-mark"></div>
</section>

<section class="sheet envelope-front">
  <svg class="edge-band" width="40" height="241" viewBox="0 0 40 241" aria-hidden="true">
    <path d="M0 0 H30 C18 70 14 150 32 241 H0 Z" fill="var(--magenta)"/>
    <path d="M36 0 C24 70 20 150 38 241" fill="none" stroke="var(--rule-grey)" stroke-width="2"/>
  </svg>
  <div class="brand">
    <div class="brand-ring"></div>
    <div class="brand-name">Lorvex Tilo</div>
    <div class="brand-tag">Tilo rise</div>
  </div>
  <div class="return-address">
    <div>2140 Fernhill Road</div>
    <div>Ashby, Oregon 58210</div>
  </div>
</section>

</body>
</html>
```